Signage Design Project

We need a logo and signage for the shopfront of a personal fitness training gym and coaching facility. We want the signage to cover the glass shopfront windows which consist of 4 glass windows with dimensions: 1 of 200cm x 180cm, 2 of 180cm x 135cm and 1 of 180cm x 180cm. The windows that are 200x 180 and 180x180 are the most visable/ important. We want the 200x180 to display the logo and our name which is "Ridgeline Fitness Centre" with further information of: Your personal training studio and boutique coaching gym Ph: 9471 2836.
For the window with 180 x 180cm measurement we want to list the services we provide which are:
Personal Training Sessions | Group Classes|Weight Loss |Toning & Sculpting|Bodybuilding I Cardio|Weights| Kettlebells| Boxing| Circuits I Team Building Programs| Boot Camp I Healthy Lifestyle & Wellness Coaching
The 2 windows 180x135cm are diagonal to the entry of the shop. We want them to be the same and plainer in design with the words: Ridgeline Fitness Centre
Personal Training Studio and Boutique Coaching Gym
The signage design also includes an acrylic window box that lights up which is to display the logo and Ridgeline Fitness Centre

```html
<!DOCTYPE html>
<html lang="en">
<head>
<meta charset="utf-8">
<title>Ridgeline Fitness Centre – Window Sign</title>
<link href="https://fonts.googleapis.com/css2?family=Arimo:wght@700&display=swap" rel="stylesheet">
<style>
  :root {
    --teal-bright: #1a9cc0;
    --teal-deep: #0a6f86;
    --lime: #a2b51f;
    --white: #ffffff;
    --frame: #444444;
    --photo-top: #e9eef2;
    --photo-bottom: #5aa9d6;
  }
  html, body {
    margin: 0;
    width: 1200px;
    height: 900px;
    overflow: hidden;
    background: var(--white);
    font-family: "Arimo", Arial, sans-serif;
  }
  .sign {
    position: absolute;
    left: 327px;
    top: 93px;
    width: 534px;
    height: 718px;
    box-sizing: border-box;
    border: 1px solid var(--frame);
    overflow: hidden;
    background: var(--white);
  }
  .sign-bands {
    position: absolute;
    inset: 0;
  }
  .brand {
    position: absolute;
    top: 130px;
    left: 0;
    right: 0;
    text-align: center;
    color: var(--teal-bright);
    font-weight: 700;
  }
  .brand-dot {
    display: block;
    width: 32px;
    height: 32px;
    margin: 0 auto 14px;
    border-radius: 50%;
    background: var(--teal-bright);
  }
  .brand-name {
    margin: 0;
    font-size: 54px;
    line-height: 1;
    letter-spacing: 2px;
    text-transform: uppercase;
  }
  .brand-name .brand-line2 {
    display: block;
    font-size: 32px;
    margin-top: 10px;
    letter-spacing: 3px;
  }
  .tagline {
    position: absolute;
    top: 334px;
    left: 0;
    right: 0;
    text-align: center;
    font-weight: 700;
    margin: 0;
  }
  .tagline-main {
    display: block;
    color: var(--lime);
    font-size: 28px;
    letter-spacing: 1px;
  }
  .tagline-sub {
    display: block;
    margin-top: 6px;
    color: var(--teal-deep);
    font-size: 21px;
    letter-spacing: 1px;
  }
  .tagline-sub .amp { color: var(--lime); }
  .hero-photo {
    position: absolute;
    left: 113px;
    top: 447px;
    width: 325px;
    height: 265px;
    border-radius: 120px 120px 40px 40px;
    background: linear-gradient(180deg, var(--photo-top), var(--photo-bottom));
    opacity: 0.9;
  }
  .corner-name {
    position: absolute;
    left: 22px;
    bottom: 28px;
    color: var(--white);
    font-size: 13px;
    font-weight: 700;
    line-height: 1.2;
    text-transform: uppercase;
  }
</style>
</head>
<body>
  <div class="sign">
    <svg class="sign-bands" viewBox="0 0 534 718" width="534" height="718" aria-hidden="true">
      <path d="M0,487 C150,585 330,655 534,630 L534,718 L0,718 Z" fill="var(--lime)"/>
      <path d="M0,545 C130,640 300,700 440,650" fill="none" stroke="var(--white)" stroke-width="5"/>
      <path d="M534,432 C505,565 425,685 270,718 L534,718 Z" fill="var(--teal-deep)"/>
    </svg>

    <div class="brand">
      <span class="brand-dot"></span>
      <h1 class="brand-name">Ridgeline<span class="brand-line2">Fitness Centre</span></h1>
    </div>

    <p class="tagline">
      <span class="tagline-main">Personal Training</span>
      <span class="tagline-sub">Studio <span class="amp">&amp;</span> Boutique Coaching Gym</span>
    </p>

    <div class="hero-photo" role="img" aria-label="Photo of a smiling woman in blue sportswear seated on the floor doing a hamstring stretch"></div>

    <div class="corner-name">Ridgeline<br>Fitness Centre</div>
  </div>
</body>
</html>
```